Business Card Design Project - del varosi group

dear Sirs

we need business card design for our group ( DEL Varosi Group ) , i have got the Logo design of our group from pixel harbor in previous , so all need details relating to our group i think available with you, as well as the the chosen logo design

we hope to provide us with business card logo that to be appropaite and satisfactory to us .

thanks

note : logo design of our group is attached .
Updates

Reason: please extend the deadline of my project for additional 15 days because i didn't received appropriate design for our gruop yet . kindly beaware that i have received 77 design till now , supossed to send me 200-250 design at least . thanks

Target Market(s)

contents

name : Kerem EL Nadiri

position : Operation Manager

Industry/Entity Type

Business

Requirements
Must have

• person name

group logo
Nice to have
• logo color matching with back background

```html
<!DOCTYPE html>
<html lang="en">
<head>
<meta charset="utf-8">
<title>DEL Varosi Group – Business Card</title>
<link rel="stylesheet" href="https://fonts.googleapis.com/css2?family=Montserrat:wght@500&family=Open+Sans:wght@400;600&display=swap">
<style>
  :root {
    --backdrop: #efe9d6;
    --navy: #1b3f7a;
    --navy-deep: #14305f;
    --gold: #d8b45a;
    --gold-light: #fbf6e6;
    --gold-dark: #c9a655;
    --white: #ffffff;
  }
  * { margin: 0; padding: 0; box-sizing: border-box; }
  html, body { width: 1200px; height: 951px; overflow: hidden; }
  body { background: var(--backdrop); position: relative; font-family: "Open Sans", Arial, sans-serif; }

  .card {
    position: absolute;
    width: 640px;
    height: 370px;
    border-radius: 26px;
    overflow: hidden;
    box-shadow: 0 8px 24px rgba(0,0,0,0.18);
  }

  /* Front */
  .card-front {
    left: 70px; top: 70px;
    background: radial-gradient(ellipse at 45% 40%, #2456a0 0%, var(--navy) 55%, var(--navy-deep) 100%);
    display: flex; flex-direction: column; align-items: center; justify-content: center;
    gap: 40px;
  }
  .brand {
    display: flex; align-items: center; gap: 16px;
    font-family: "Montserrat", Arial, sans-serif;
    font-weight: 500;
    letter-spacing: 1px;
    white-space: nowrap;
  }
  .brand-mark { display: block; flex: none; }
  .card-front .brand { color: var(--white); font-size: 46px; }
  .card-front .brand-mark { width: 22px; height: 22px; background: var(--gold); }
  .card-front .web { color: var(--gold); font-size: 19px; letter-spacing: 2px; }

  /* Back */
  .card-back {
    left: 490px; top: 500px;
    background: linear-gradient(180deg, #1f4a8c 0%, var(--navy) 60%, var(--navy-deep) 100%);
  }
  .gold-panel {
    position: absolute; right: 0; top: 0; bottom: 0; width: 270px;
    border-radius: 36px 0 0 36px;
    background: linear-gradient(90deg, var(--gold-dark) 0%, var(--gold-light) 40%, var(--gold-light) 55%, var(--gold) 100%);
    display: flex; align-items: center; justify-content: center;
    padding: 0 16px;
  }
  .gold-panel .brand {
    color: var(--navy); font-size: 18px; gap: 8px; letter-spacing: 0.5px;
  }
  .gold-panel .brand-mark { width: 10px; height: 10px; background: var(--navy); }

  .contact { position: absolute; left: 48px; top: 34px; color: var(--white); }
  .person-name { color: var(--gold); font-size: 21px; font-weight: 600; }
  .person-role { font-size: 15px; margin-top: 2px; }
  .address { display: flex; gap: 10px; margin-top: 30px; font-size: 16px; line-height: 1.3; }
  .lines { margin-top: 18px; font-size: 16px; line-height: 1.45; }
  .line { display: flex; align-items: center; gap: 10px; }
  .icon { width: 14px; height: 14px; flex: none; fill: var(--gold); }
</style>
</head>
<body>

<section class="card card-front" aria-label="Card front">
  <div class="brand"><span class="brand-mark"></span>DEL VAROSI GROUP</div>
  <div class="web">www.delvarosigroup.com</div>
</section>

<section class="card card-back" aria-label="Card back">
  <div class="contact">
    <div class="person-name">Kerem EL Nadiri</div>
    <div class="person-role">Operation Manager</div>

    <div class="address">
      <svg class="icon" viewBox="0 0 14 14" aria-hidden="true"><path d="M7 1 L13 7 H11 V13 H8.5 V9 H5.5 V13 H3 V7 H1 Z"/></svg>
      <div>1450 Orvell Park Rd.<br>Suite 204-118<br>Marlow, TX 78140</div>
    </div>

    <div class="lines">
      <div class="line">
        <svg class="icon" viewBox="0 0 14 14" aria-hidden="true"><path d="M3 1 L5.5 1 L6.5 4 L5 5.2 C5.8 7 7 8.2 8.8 9 L10 7.5 L13 8.5 V11 C13 12 12 13 11 13 C5.5 12.5 1.5 8.5 1 3 C1 2 2 1 3 1 Z"/></svg>
        555-014-2290
      </div>
      <div class="line">
        <svg class="icon" viewBox="0 0 14 14" aria-hidden="true"><rect x="1" y="4" width="12" height="8" rx="1"/><rect x="3.5" y="1" width="7" height="4" fill="var(--navy)" stroke="var(--gold)" stroke-width="1.2"/></svg>
        555-014-2291
      </div>
      <div class="line">
        <svg class="icon" viewBox="0 0 14 14" aria-hidden="true"><rect x="1" y="3" width="12" height="8" rx="1"/><path d="M1.5 3.5 L7 8 L12.5 3.5" fill="none" stroke="var(--navy)" stroke-width="1.2"/></svg>
        info@delvarosigroup.com
      </div>
      <div class="line">
        <svg class="icon" viewBox="0 0 14 14" aria-hidden="true"><circle cx="7" cy="7" r="6"/></svg>
        www.delvarosigroup.com
      </div>
    </div>
  </div>

  <div class="gold-panel">
    <div class="brand"><span class="brand-mark"></span>DEL VAROSI GROUP</div>
  </div>
</section>

</body>
</html>
```